Church Website with Home Page and Member Sermon Library

I am in need of an updated design for our church website. This will include 4 pages (outlined below). We are a conservative, evangelical, Christian church. The site should be modern and clean, while still reflecting our conservative values. I already have a logo for our church, and I want the site to incorporate the logo, and match the logo/branding. Stock photos are allowed if needed, but I have uploaded some images of our church and would prefer those images to be used if possible. Any stock photos used should not include any people in the photos (scenery, nature, buildings, animals, etc. are fine).

The site will need 4 pages: Home, Support Us (Donate), Login, and Recording Library.

Page 1: Home
The home page should include the following sections:

- Navigation: Should include links to each section of the home page plus a "listen live" link which will take the user to a live-streaming site and a "support us" link which will take the user to a support/donate page.

- Announcements: Can be either a banner or some other design, but there needs to be some way for us to post announcements for visitors to see. I'm open for creative ideas in this section, but would like it not to take up a lot of room on the page.

- About Us: Should include address, service times (see attached document), and information about the church.

- Pastor Bio: A section that introduces our pastor and gives a short bio about our pastor. Would like this section to include a picture of our pastor. Somewhere in this section I would like to include this Bible reference: "And I will give you pastors according to mine heart, which shall feed you with knowledge and understanding. Jer 3:15 LPW"

- Articles of Faith (What We Believe): This should include several sub-sections each with a heading, body, and possibly 1 or more scripture references. I have attached a document to the brief that includes our articles of faith. Feel free to be creative with this section in how you lay these out and format them.

- Support Us: A small section that explains what kind of support someone can give and a link to a donation page. The link can say something like "Support Us" or "Donate Now".

- Contact form: A contact form that allows the visitor to send us a message. The contact form should ask for name, email, phone, and message.

- Footer: A footer that will be displayed on all pages of the site. This should include at a minimum a link to the home page (or a link to each individual section in the home page if you prefer), a link to "listen live", a link to "support us", a link to "contact us" (or you can put the contact form directly in the footer if you prefer), the address, and a "member login" link.

Page 2: Support Us
The donation page should include a form the visitor can fill out to make a donation. We will embed a third party form later. For this design, please just mock out the design with a basic form asking for name, phone, and email.

Page 3: Login
The recording library (detailed below) will require members to login with a shared numeric code before accessing the page. We need a design for a login screen. The screen should include navigation/footer just like all other pages, but the body of the login page will consist only of a form that asks the user to enter the access code and then a "login" button.

Page 4: Recording Library

The library page is a member-only page that will require a shared, numeric pass code to access. On this page, members will be able to access a filterable list of past sermons. The page by default should display most recent sermons, but should also include a search form that allows the member to filter the sermon list to find a particular sermon. The search form should allow the user to select a filter type (e.g. Speaker name, date, event, etc.) and type in a value to search. They should be able to add multiple filters and remove filters that have been added. Each sermon that is displayed in the result list should include basic information such as title, date, speaker, tags, etc. along with a download icon, and an embedded audio player where they can click a play button to stream it on-demand. Each sermon should also have clickable tags associated with it that can be used to find related sermons.
Updates

I have uploaded several images of our church. Feel free to incorporate these into your design if possible.

Target Market(s)

Church Members

Industry/Entity Type

Religion

Number of Pages Required

4 page

Font styles to use
Sans Serif

Colors

Designer to choose colors to be used in the design.

Requirements
Must have
• Must incorporate the logo (attached)
Nice to have
• Would like the design to incorporate pictures of our church (attached) instead of stock photos if possible.
Should not have
• Please avoid an overly cluttered design. Stock photos used should not include any people in the photos.

```html
<!DOCTYPE html>
<html lang="en">
<head>
<meta charset="utf-8">
<title>Harbor Light Church</title>
<link href="https://fonts.googleapis.com/css2?family=Cinzel:wght@400;500&family=Poppins:wght@300;400;500;600&display=swap" rel="stylesheet">
<style>
:root{
  --teal:#0db5d3;
  --teal-dark:#0aa3bf;
  --green-light:#8db56a;
  --green-dark:#3e5e22;
  --text:#444;
  --muted:#666;
  --line:#e2e2e2;
  --footer:#1b1b1b;
  --white:#fff;
}
*{box-sizing:border-box;margin:0;padding:0}
html,body{width:1200px;height:3551px;overflow:hidden}
body{position:relative;font-family:"Poppins",sans-serif;color:var(--text);background:var(--white)}
.abs{position:absolute}
a{color:inherit;text-decoration:none}
.serif{font-family:"Cinzel",serif}
.btn{position:absolute;background:var(--teal);color:var(--white);font-size:14px;font-weight:500;display:flex;align-items:center;justify-content:center;border-radius:3px}
.caps{text-transform:uppercase}

/* hero */
.hero{left:0;top:0;width:1200px;height:608px;background:linear-gradient(180deg,#5a5a5a 0%,#7d6e62 45%,#8a7868 70%,#c9c4c0 100%)}
.brand{left:150px;top:44px;width:170px;text-align:center;color:var(--white);font-weight:400;font-size:22px;letter-spacing:1px;line-height:1.25}
.nav{left:459px;top:50px;font-size:13.5px;color:var(--white)}
.nav a{position:absolute;white-space:nowrap}
.hero-title{left:163px;top:240px;font-family:"Cinzel",serif;font-weight:400;font-size:52px;line-height:1.1;color:var(--white);letter-spacing:1px}
.hero-text{left:163px;top:310px;width:500px;color:var(--white);font-size:14.5px;line-height:25.5px;font-weight:500}

/* about */
.about{left:0;top:608px;width:1200px;height:624px;background:linear-gradient(180deg,#fff 0%,#fff 25%,#f4f0ec 60%,#e7d8d4 100%)}
.kicker{position:absolute;left:0;width:1200px;text-align:center;color:var(--green-light);font-size:14px}
.title{position:absolute;left:0;width:1200px;text-align:center;font-family:"Cinzel",serif;font-size:36px;line-height:1.2;color:var(--green-dark)}
.title .lt{color:var(--green-light)}
.center-p{position:absolute;left:210px;width:780px;text-align:center;font-size:14px;line-height:24px;color:#333}
.service{left:274px;top:1050px;width:641px;height:96px;background:var(--teal);border-radius:6px;color:var(--white);overflow:hidden}
.service .clock{position:absolute;left:0;top:0;width:108px;height:96px;background:var(--teal-dark)}
.service .txt{position:absolute;top:14px;font-size:13.5px;font-weight:500;line-height:24px}

/* pastor */
.pastor{left:0;top:1232px;width:1200px;height:598px;background:#f6f6f6;border-bottom:1px solid var(--line)}
.pastor-photo{left:128px;top:1297px;width:378px;height:533px}
.bio{left:613px;width:430px}

/* articles */
.faith-list{left:160px;top:1988px;width:200px;border-top:1px solid var(--line)}
.faith-list li{list-style:none;height:39px;line-height:39px;padding-left:12px;font-size:14px;color:#555;border-bottom:1px solid var(--line)}
.faith-list li.active{background:var(--teal);color:var(--white);border-radius:3px;font-weight:500}
.check{font-size:14px;color:#555;display:flex;align-items:center;gap:6px}

/* support */
.support{left:0;top:2356px;width:1200px;height:338px;background:linear-gradient(180deg,#e9e9e9,#f3f3f3 50%,#e6e6e6)}

/* contact */
.field{position:absolute;border:1px solid #d6d6d6;border-radius:3px;background:var(--white);font-size:12.5px;color:#333}
.field .ic{position:absolute;left:0;top:0;width:38px;height:100%;border-right:1px solid #e2e2e2}
.field .ic svg{position:absolute;left:12px;top:14px}
.field span{position:absolute;left:57px;top:13px}

/* footer */
.footer-bg{left:0;top:3207px;width:1200px;height:344px;background:var(--footer)}
.footer{left:0;top:3207px;width:1200px;height:344px;color:#e8e8e8}
.footer h4{position:absolute;font-family:"Cinzel",serif;font-weight:400;font-size:18px;letter-spacing:2px;color:var(--white)}
.footer .small{position:absolute;font-size:12.5px;line-height:27px}
</style>
</head>
<body>

<!-- HERO -->
<section class="abs hero" role="img" aria-label="Photo of the brick church building under a grey sky"></section>
<div class="abs brand">Harbor Light<br><span style="font-size:12px;letter-spacing:5px">CHURCH</span></div>
<nav class="abs nav">
  <a style="left:0">Home</a>
  <a style="left:79px">Donate</a>
  <a style="left:169px">Login</a>
  <a style="left:243px">Recording Library</a>
  <a style="left:400px">Listen Live</a>
  <a style="left:507px">Support Us</a>
</nav>
<h1 class="abs hero-title">ANNOUNCEMENTS</h1>
<p class="abs hero-text">Lorem ipsum dolor sit amet, consectetuer adipiscing elit sed diam nonummy nibh euismod tincidunt ut laoreet dolore magna aliquam erat volutpat. Ut wisi enim ad minim veniam.</p>
<a class="btn caps" style="left:163px;top:408px;width:122px;height:36px;font-size:13.5px">Know More</a>

<!-- ABOUT -->
<section class="abs about" role="img" aria-label="Faded photo of the church sanctuary with wooden pews and red aisle"></section>
<div class="kicker caps" style="top:693px">About Harbor Light</div>
<h2 class="title caps" style="top:712px;font-weight:400"><span class="lt">Harbor Light</span> Church</h2>
<p class="center-p" style="top:779px">Lorem ipsum dolor sit amet, consectetuer adipiscing elit, sed diam nonummy nibh euismod tincidunt ut laoreet dolore magna aliquam erat volutpat. Ut wisi enim ad minim veniam, quis nostrud exerci tation ullamcorper suscipit lobortis nisl ut aliquip ex ea commodo consequat.</p>
<p class="center-p" style="top:858px">Duis autem vel eum iriure dolor in hendrerit in vulputate velit esse molestie consequat, vel illum dolore eu feugiat nulla facilisis at vero eros et accumsan et iusto odio dignissim qui blandit praesent.</p>
<div class="abs" style="left:397px;top:916px;display:flex;align-items:center;gap:10px;font-size:14px;color:#333">
  <svg width="38" height="38" viewBox="0 0 38 38"><circle cx="19" cy="19" r="17.5" fill="none" stroke="var(--green-dark)" stroke-width="1.5"/><path d="M19 9c-4 0-7 3-7 7 0 5 7 13 7 13s7-8 7-13c0-4-3-7-7-7z" fill="var(--green-dark)"/><circle cx="19" cy="16" r="2.6" fill="#fff"/></svg>
  <span>42 Maple Ridge Lane, Laramie, WY 82070 &nbsp;United States</span>
</div>
<a class="btn" style="left:528px;top:966px;width:142px;height:45px;font-size:15px">Donate Now</a>
<div class="abs service">
  <div class="clock"><svg width="108" height="96" viewBox="0 0 108 96"><circle cx="54" cy="48" r="18" fill="none" stroke="#fff" stroke-width="3"/><path d="M54 37v12h9" fill="none" stroke="#fff" stroke-width="3" stroke-linecap="round"/></svg></div>
  <div class="txt" style="left:127px">Service Times :<br>Wednesday Evening Service: 7:30 PM<br>Sunday School : 10:00 AM</div>
  <div class="txt" style="left:411px;top:38px">Sunday Morning Service: 11:00<br>Sunday Evening Service: 5:30</div>
</div>

<!-- PASTOR -->
<section class="abs pastor" role="img" aria-label="Faint photo of a church interior with arches"></section>
<svg class="abs" style="left:160px;top:1297px" width="276" height="300" viewBox="0 0 276 300"><path d="M8 300V150C8 80 70 30 138 0c68 30 130 80 130 150v150" fill="none" stroke="var(--teal)" stroke-width="16"/></svg>
<div class="abs pastor-photo" role="img" aria-label="Portrait photo of the pastor" style="background:linear-gradient(180deg,#eeeeee,#d8d8d8 60%,#cfcfcf)"></div>
<div class="abs bio" style="top:1359px;font-size:14px;color:var(--green-light)">BIOGRAPHY</div>
<h2 class="abs bio serif" style="top:1372px;font-size:34px;font-weight:400;line-height:1.2;color:var(--green-dark)">PASTOR BIO</h2>
<p class="abs bio" style="top:1422px;width:410px;font-size:15px;font-weight:600;line-height:23px;color:#333">"I will give you pastors according to mine heart, which shall feed you with knowledge and understanding. Jer 3:15 LPW"</p>
<p class="abs bio" style="top:1497px;width:432px;font-size:13px;line-height:24.5px;color:#555">Lorem ipsum dolor sit amet, consectetuer adipiscing elit, sed diam nonummy nibh euismod tincidunt ut laoreet ore magna aliquam erat volutpat. Ut wisi enim ad minim ven quis nostrud exerci tation ullamcorper suscipit lobortis nisl ut aliquip ex ea commodo consequat. Duis autem vel eum iriuror in hendrerit in vulputate velit esse molestie consequat, vel illum dolore eu feugiat nulla facilisis at vero eros et accumsan.</p>
<a class="btn caps" style="left:614px;top:1694px;width:123px;height:36px;font-size:13.5px">Contact Me</a>

<!-- ARTICLES OF FAITH -->
<h2 class="title caps" style="top:1908px;font-weight:400;letter-spacing:1px"><span class="lt">Articles</span> of Faith</h2>
<ul class="abs faith-list">
  <li>The God Head.</li>
  <li class="active">Full Salvation.</li>
  <li>Sanctification.</li>
  <li>Baptism of the Holy Ghost.</li>
  <li>Divine Healing.</li>
  <li>Second coming of Christ.</li>
  <li>Eternity</li>
</ul>
<h3 class="abs serif" style="left:429px;top:2003px;font-size:31px;font-weight:400;line-height:1.2;color:var(--green-dark)">Full Salvation</h3>
<p class="abs" style="left:429px;top:2052px;width:608px;font-size:14px;line-height:23px;color:#555">We believe that Salvation is received only when a person comes to the realization that he or she is lost and separated from God and becomes full of godly sorrow, confessing their sins and true repentance, believing in the shed blood of the Lord Jesus Christ as the only sacrifice for sins.Through the blood of Christ we have:</p>
<svg width="0" height="0" style="position:absolute"><symbol id="tick" viewBox="0 0 14 14"><circle cx="7" cy="7" r="6" fill="none" stroke="var(--teal)" stroke-width="1.3"/><path d="M4.2 7.2l2 2 3.6-4" fill="none" stroke="var(--teal)" stroke-width="1.3"/></symbol></svg>
<div class="abs check" style="left:429px;top:2161px"><svg width="13" height="13"><use href="#tick"/></svg>Remission of Sins, Matthew 26:28 Heb 9:22</div>
<div class="abs check" style="left:429px;top:2191px"><svg width="13" height="13"><use href="#tick"/></svg>Sanctification. Hebrews 13:12</div>
<div class="abs check" style="left:429px;top:2221px"><svg width="13" height="13"><use href="#tick"/></svg>Redemption. Revelations 5:9</div>
<div class="abs check" style="left:788px;top:2161px"><svg width="13" height="13"><use href="#tick"/></svg>Cleansing. 1 John 1:7 Rev. 1:5</div>
<div class="abs check" style="left:788px;top:2191px"><svg width="13" height="13"><use href="#tick"/></svg>Justification. Romans 5:9</div>

<!-- SUPPORT -->
<section class="abs support" role="img" aria-label="Faded photo of a library with tall bookshelves"></section>
<div class="kicker caps" style="top:2443px">Remaining to helps</div>
<h2 class="title caps" style="top:2458px;font-size:47px;font-weight:500">Support Us</h2>
<p class="center-p" style="left:240px;width:720px;top:2517px;font-size:17.5px;line-height:29px;color:#555">Lorem ipsum dolor sit amet, consectetuer adipiscing elit, sed diam nonummy nibh euismod tincidunt ut laoreet dolore magna aliquam erat volutpat.</p>
<a class="btn caps" style="left:538px;top:2603px;width:124px;height:34px;font-size:13.5px">Donate Now</a>

<!-- CONTACT -->
<h2 class="title caps" style="top:2776px;font-weight:400"><span class="lt">Contact</span> Us</h2>
<svg width="0" height="0" style="position:absolute">
  <symbol id="user" viewBox="0 0 14 14"><circle cx="7" cy="4" r="3" fill="var(--green-light)"/><path d="M1 13c0-4 3-5 6-5s6 1 6 5z" fill="var(--green-light)"/></symbol>
  <symbol id="phone" viewBox="0 0 14 14"><path d="M3 1l2.5 3-1.5 1.5c1 2 2.5 3.5 4.5 4.5L10 8.5l3 2.5-1.5 2C6 13 1 8 1 2.5z" fill="var(--green-light)"/></symbol>
  <symbol id="mail" viewBox="0 0 14 14"><rect x="1" y="3" width="12" height="9" fill="var(--green-light)"/><path d="M1 3l6 5 6-5" fill="none" stroke="#fff" stroke-width="1"/></symbol>
  <symbol id="chat" viewBox="0 0 14 14"><path d="M1 2h8v5H4l-3 2z" fill="var(--green-light)"/><path d="M10 5h3v5l-2-1.5H6V8h4z" fill="var(--green-light)"/></symbol>
</svg>
<div class="field" style="left:284px;top:2845px;width:308px;height:43px"><div class="ic"><svg width="14" height="14"><use href="#user"/></svg></div><span>First Name*</span></div>
<div class="field" style="left:608px;top:2845px;width:308px;height:43px"><div class="ic"><svg width="14" height="14"><use href="#user"/></svg></div><span>Last Name*</span></div>
<div class="field" style="left:284px;top:2904px;width:308px;height:44px"><div class="ic"><svg width="14" height="14"><use href="#phone"/></svg></div><span>Your Phone*</span></div>
<div class="field" style="left:608px;top:2904px;width:308px;height:44px"><div class="ic"><svg width="14" height="14"><use href="#mail"/></svg></div><span>Your Email*</span></div>
<div class="field" style="left:284px;top:2963px;width:632px;height:88px"><div class="ic"><svg width="14" height="14"><use href="#chat"/></svg></div><span>Your Message</span></div>
<a class="btn caps" style="left:538px;top:3081px;width:124px;height:36px;font-size:13.5px">Submit Now</a>

<!-- FOOTER -->
<div class="abs footer-bg" role="img" aria-label="Dark photo of a church interior"></div>
<footer class="abs footer">
  <h4 style="left:163px;top:78px">Quick Links</h4>
  <div class="small" style="left:163px;top:107px"><a style="text-decoration:underline">Home</a><br>Donate<br>Login</div>
  <div class="small" style="left:247px;top:109px">Recording Library<br>Listen Live<br>Support Us</div>
  <h4 style="left:490px;top:76px">Contact Info</h4>
  <div class="small" style="left:490px;top:107px;line-height:21px">42 Maple Ridge Lane, Laramie, WY<br>82070 &nbsp;United States</div>
  <div class="small" style="left:490px;top:160px">info@harborlightchurch.org</div>
  <div class="small" style="left:490px;top:192px;font-size:16px;letter-spacing:.5px">(555) 014-2290</div>
  <div class="abs" style="left:800px;top:122px;width:132px;text-align:center;font-size:19px;color:#fff;line-height:1.3">Harbor Light<br><span style="font-size:10px;letter-spacing:5px">CHURCH</span></div>
  <div class="abs" style="left:964px;top:145px;display:flex;align-items:center;gap:7px;font-size:17px;font-weight:600;color:#fff"><span style="width:14px;height:14px;border:2px solid #fff;border-radius:50%"></span>Streamly</div>
  <div class="abs" style="left:163px;top:296px;width:874px;height:1px;background:#3a3a3a"></div>
  <div class="abs" style="left:0;top:313px;width:1200px;text-align:center;font-size:12.5px">© 2023 Harbor Light Church. All Rights Reserved.</div>
</footer>

</body>
</html>
```